Food and Beverage Business Cards

We need business cards with logo designs for a consultant in the food and beverage industry. We specialize in helping restaurants fix operational and management problems.
Specific areas of expertise include:
-Steps of service
-Staff management tools
-Standard operating procedures
-Profit and loss management
-Inventory
-Point of sales
-Bar Menu
-Mystery shopper service
-Handling and managing suppliers

Target Market(s)

Restaurant and bar owners and managers

Industry/Entity Type

Business

Contact Information for Business Card

Mathieu Girardot
Q&T Consulting
phone: 15027390614
mathqt@sampleinbox.com

Font styles to use
Other font styles liked:
• Check out the screen shot font idea

Colors

Designer to choose colors to be used in the design.

Requirements
Must have
• Must include QR code (See attachment)
• Logo should reflect our specific focus on the drinks side of the industry.
• Areas of Expertise:
• -Service Steps
• -Staff management tools
• -S.O.P
• -P&L Management
• -Inventory
• -P.O.S
• -Bar Menu
• -Mystery Shopper Service
• -Handling and Managing Suppliers

```html
<!DOCTYPE html>
<html lang="en">
<head>
<meta charset="utf-8">
<title>Q&amp;T Marlow – Business Cards</title>
<link rel="stylesheet" href="https://fonts.googleapis.com/css2?family=Open+Sans:wght@400;600;700&display=swap">
<style>
  :root {
    --backdrop: #3a3a3c;
    --card-black: #0d0d0d;
    --card-white: #f4f4f4;
    --swoosh-grey: #8a8a8a;
    --ink-dark: #1a1a1a;
    --ink-light: #ffffff;
    --ink-muted: #d8d8d8;
    --badge-green: #3f8f3a;
    --badge-grey: #5a5a5a;
    --badge-light: #e6e6e6;
  }
  * { box-sizing: border-box; margin: 0; padding: 0; }
  html, body {
    width: 1200px; height: 960px; overflow: hidden;
    background: var(--backdrop);
    font-family: "Open Sans", Arial, sans-serif;
  }
  .sheet {
    width: 1200px; height: 960px;
    display: flex; flex-direction: column; align-items: center; justify-content: center;
    gap: 40px;
  }
  .card {
    position: relative; width: 700px; height: 400px; overflow: hidden;
    box-shadow: 0 10px 30px rgba(0,0,0,.45);
  }
  .brand-name {
    font-family: "Open Sans", Arial, sans-serif;
    font-weight: 600; letter-spacing: 1px; line-height: 1;
  }

  /* Back side */
  .card-back { background: var(--card-black); color: var(--ink-light); }
  .card-back .badges {
    position: absolute; top: 26px; right: 28px; display: flex; gap: 12px;
  }
  .badge { width: 52px; height: 52px; border-radius: 50%; }
  .badge-green { background: var(--badge-green); }
  .badge-grey { background: var(--badge-grey); border: 2px solid var(--badge-light); }
  .badge-light { background: var(--badge-light); }
  .card-back .brand-name {
    position: absolute; top: 120px; left: 0; width: 100%; text-align: center;
    font-size: 64px; color: var(--ink-light);
  }
  .expertise {
    position: absolute; top: 232px; left: 0; width: 100%; text-align: center;
  }
  .expertise-title { font-size: 22px; font-weight: 700; margin-bottom: 10px; }
  .expertise-list { font-size: 16px; line-height: 1.55; color: var(--ink-muted); }

  /* Front side */
  .card-front { background: var(--card-white); }
  .card-front .brand-name {
    position: absolute; top: 56px; left: 60px;
    font-size: 72px; color: var(--ink-dark);
  }
  .card-front .curve { position: absolute; inset: 0; }
  .contact {
    position: absolute; right: 34px; bottom: 34px; text-align: right; color: var(--ink-light);
  }
  .contact-name { font-size: 26px; font-weight: 700; letter-spacing: .5px; }
  .contact-company { font-size: 19px; color: var(--ink-muted); margin-bottom: 22px; letter-spacing: .5px; }
  .contact-line { display: flex; justify-content: flex-end; align-items: center; gap: 10px; font-size: 19px; line-height: 1.5; }
  .contact-line svg { width: 18px; height: 18px; fill: var(--ink-light); }
</style>
</head>
<body>
<main class="sheet">

  <section class="card card-back" aria-label="Card back">
    <div class="badges">
      <span class="badge badge-green"></span>
      <span class="badge badge-grey"></span>
      <span class="badge badge-light"></span>
    </div>
    <div class="brand-name">Q&amp;T Marlow</div>
    <div class="expertise">
      <p class="expertise-title">Areas of Expertise</p>
      <p class="expertise-list">Service Steps | Staff management tools | S.O.P | P&amp;L Management<br>
      Inventory | P.O.S | Bar Menu | Mystery Shopper Service<br>
      Handling and Managing Suppliers</p>
    </div>
  </section>

  <section class="card card-front" aria-label="Card front">
    <div class="brand-name">Q&amp;T Marlow</div>
    <svg class="curve" viewBox="0 0 700 400" preserveAspectRatio="none" aria-hidden="true">
      <defs>
        <linearGradient id="swoosh-fade" x1="0" x2="1" y1="0" y2="0">
          <stop offset="0" stop-color="var(--swoosh-grey)" stop-opacity="0"/>
          <stop offset=".35" stop-color="var(--swoosh-grey)" stop-opacity="1"/>
          <stop offset="1" stop-color="var(--swoosh-grey)" stop-opacity=".6"/>
        </linearGradient>
      </defs>
      <path d="M0,352 C200,236 450,178 700,192 L700,212 C450,200 200,258 0,372 Z" fill="url(#swoosh-fade)"/>
      <path d="M0,380 C200,266 450,212 700,222 L700,400 L0,400 Z" fill="var(--card-black)"/>
    </svg>
    <div class="contact">
      <p class="contact-name">MATHIEU GIRARDOT</p>
      <p class="contact-company">Q&amp;T CONSULTING</p>
      <p class="contact-line">15027390614
        <svg viewBox="0 0 24 24" aria-hidden="true"><path d="M6.6 10.8a15.1 15.1 0 0 0 6.6 6.6l2.2-2.2c.3-.3.7-.4 1-.2 1.1.4 2.3.6 3.6.6.6 0 1 .4 1 1V20c0 .6-.4 1-1 1C10.6 21 3 13.4 3 4c0-.6.4-1 1-1h3.5c.6 0 1 .4 1 1 0 1.3.2 2.5.6 3.6.1.3 0 .7-.2 1z"/></svg>
      </p>
      <p class="contact-line">mathqt@sampleinbox.com
        <svg viewBox="0 0 24 24" aria-hidden="true"><path d="M3 5h18v14H3z M3 5l9 7 9-7" fill="none" stroke="#fff" stroke-width="2"/></svg>
      </p>
    </div>
  </section>

</main>
</body>
</html>
```